Velmora Trading Company product labels (5"wide x7" high (12,5 cm x 17,5 cm))

We need a vertical product label that will go on the Gold stand up bags for our Kratom powder. We are looking for professional looking and attractive label design that will capture the attention of consumers. Our products should stand out when sitting on a shelf next to our competitors. We want one label which we will be able to use for all the different Kratom Powders we have.The product label will be used for several different varieties of Kratom so there will need to be an area available for the varieties name such as "RED BORNEO" or "GREEN MAENG DA" etc., which we will apply a small label as needed.
The label dimensions should be 5" wide x 7" high (12,5 cm wide x 17,5 cm high).
Please review the "must haves" section, and please try and include the "nice to haves" if possible.

Target Market(s)

Health minded consumers who love natural products, and are looking for plant based alternatives to harmful synthetic products.

Industry/Entity Type

Supplement

Colors

Designer to choose colors to be used in the design.

Requirements
Must have
• Product labels must include:
• 1) Company logo (find in the attachments)
• 2) Product information (find in the attachments)
• 3) Product title - Premium Kratom Powder
• 4) Weight indication - 250 grams
• 5) Barcode
• 6) Icon that says - 100% pure (or "100% natural")
Nice to have
• Indonesian jungle theme.
• Our packaging is gold metallic stand up bag, so the colors should be complimenting the bag.
Should not have
• labels or part of the labels taken from other Kratom companies. The design should be unique.

```html
<!DOCTYPE html>
<html lang="en">
<head>
<meta charset="utf-8">
<title>Velmora Trading Company – Premium Kratom Powder Label</title>
<link rel="stylesheet" href="https://fonts.googleapis.com/css2?family=Montserrat:wght@500;600;700;800&display=swap">
<style>
  :root {
    --page: #e9eaeb;
    --forest: #2a3b1f;
    --leaf: #5a8a32;
    --leaf-soft: #7fae4e;
    --mint-top: #cfe6e4;
    --mint-bottom: #f1f6f3;
    --white: #ffffff;
    --ink: #23301a;
  }
  * { margin: 0; padding: 0; box-sizing: border-box; }
  html, body { width: 1200px; height: 847px; overflow: hidden; }
  body {
    background: var(--page);
    font-family: "Montserrat", sans-serif;
    position: relative;
  }
  .label {
    position: absolute;
    top: 78px;
    width: 492px;
    height: 690px;
    overflow: hidden;
    background: linear-gradient(180deg, var(--mint-top) 0%, var(--mint-bottom) 70%, #e6f1dc 100%);
    box-shadow: 0 4px 14px rgba(0,0,0,.18);
  }
  .label--front { left: 98px; }
  .label--back { left: 610px; }

  .foliage { position: absolute; }
  .foliage--top-left {
    left: 0; top: 0; width: 160px; height: 260px;
    background: radial-gradient(ellipse at 20% 30%, #6fa243 0%, #9cc96a 45%, rgba(190,225,160,0) 75%);
  }
  .foliage--top-right {
    right: 0; top: 0; width: 160px; height: 210px;
    background: radial-gradient(ellipse at 75% 25%, #f7f3df 0%, #8cbf5c 35%, rgba(170,215,130,0) 75%);
  }
  .foliage--bottom {
    left: 0; bottom: 0; width: 492px; height: 200px;
    background: radial-gradient(ellipse at 15% 85%, #5e963a 0%, rgba(130,185,90,.7) 35%, rgba(190,225,160,0) 65%),
                radial-gradient(ellipse at 85% 75%, #f2b3a5 0%, #8cc062 35%, rgba(190,225,160,0) 65%);
  }

  .banner { position: absolute; left: 149px; width: 195px; }
  .banner svg { display: block; }
  .banner--top { top: 0; height: 254px; }
  .banner--bottom { top: 437px; height: 253px; }

  .brand {
    position: absolute; left: 0; top: 84px; width: 195px;
    display: flex; flex-direction: column; align-items: center; gap: 8px;
    color: var(--white); text-align: center;
  }
  .brand__dot { width: 22px; height: 22px; border: 3px solid var(--white); border-radius: 50%; }
  .brand__name { font-weight: 700; font-size: 17px; line-height: 1.2; letter-spacing: .5px; text-transform: uppercase; }

  .title {
    position: absolute; left: 0; top: 290px; width: 492px; text-align: center;
    font-weight: 800; font-size: 80px; line-height: 1; letter-spacing: -1px; color: var(--forest);
  }
  .subtitle {
    position: absolute; left: 0; top: 372px; width: 492px; text-align: center;
    font-weight: 700; font-size: 29px; color: var(--leaf);
  }

  .seal {
    position: absolute; left: 0; top: 56px; width: 195px;
    display: flex; flex-direction: column; align-items: center; color: var(--white);
  }
  .seal__percent { font-weight: 800; font-size: 32px; line-height: 1; }
  .seal__word {
    margin-top: 6px; padding: 4px 18px; background: var(--leaf);
    font-weight: 700; font-size: 28px; line-height: 1.1;
  }
  .weight {
    position: absolute; left: 0; top: 185px; width: 195px; text-align: center;
    color: var(--white); font-weight: 600; font-size: 18px;
  }

  .info {
    position: absolute; left: 40px; width: 412px; text-align: center; color: var(--ink);
  }
  .info--ingredients { top: 270px; font-size: 13px; font-weight: 600; line-height: 17px; }
  .info--warning { top: 330px; font-size: 13px; font-weight: 600; line-height: 16.5px; text-transform: uppercase; }
  .info--disclaimer { top: 392px; font-size: 10px; font-weight: 500; line-height: 13px; padding: 0 50px; }
  .info--distributor { top: 482px; font-size: 13px; font-weight: 600; line-height: 16.5px; }

  .barcode-area {
    position: absolute; left: 141px; top: 573px; width: 209px; height: 57px;
    background: var(--forest); color: var(--white);
    display: flex; align-items: center; justify-content: center;
    font-size: 13px; font-weight: 500;
  }
</style>
</head>
<body>

  <section class="label label--front">
    <div class="foliage foliage--top-left" role="img" aria-label="Tropical jungle leaves with pink frangipani flower"></div>
    <div class="foliage foliage--top-right" role="img" aria-label="Palm fronds with white frangipani flower"></div>
    <div class="foliage foliage--bottom" role="img" aria-label="Jungle foliage with hibiscus and bird of paradise flowers"></div>

    <div class="banner banner--top">
      <svg width="195" height="254" viewBox="0 0 195 254" aria-hidden="true">
        <polygon points="0,0 195,0 195,254 97.5,230 0,254" fill="var(--forest)"/>
      </svg>
      <div class="brand">
        <span class="brand__dot"></span>
        <span class="brand__name">Velmora<br>Trading Company</span>
      </div>
    </div>

    <h1 class="title">PREMIUM</h1>
    <p class="subtitle">KRATOM POWDER</p>

    <div class="banner banner--bottom">
      <svg width="195" height="253" viewBox="0 0 195 253" aria-hidden="true">
        <polygon points="0,0 97.5,23 195,0 195,253 0,253" fill="var(--forest)"/>
      </svg>
      <div class="seal">
        <span class="seal__percent">100%</span>
        <span class="seal__word">natural</span>
      </div>
      <p class="weight">250 grams</p>
    </div>
  </section>

  <section class="label label--back">
    <div class="foliage foliage--top-left" role="img" aria-label="Tropical jungle leaves with pink frangipani flower"></div>
    <div class="foliage foliage--top-right" role="img" aria-label="Palm fronds with white frangipani flower"></div>
    <div class="foliage foliage--bottom" role="img" aria-label="Jungle foliage with hibiscus and bird of paradise flowers"></div>

    <div class="banner banner--top">
      <svg width="195" height="254" viewBox="0 0 195 254" aria-hidden="true">
        <polygon points="0,0 195,0 195,254 97.5,230 0,254" fill="var(--forest)"/>
      </svg>
      <div class="brand">
        <span class="brand__dot"></span>
        <span class="brand__name">Velmora<br>Trading Company</span>
      </div>
    </div>

    <p class="info info--ingredients">INGREDIENTS:<br>100% natural Mitragyna Speciosa leaf powder.</p>
    <p class="info info--warning">Not for sale to minors.<br>Must be 18 years or older to purchase.<br>Keep out of reach of children.</p>
    <p class="info info--disclaimer">Do not use any botanicals without a physician's consent, if you are a minor, pregnant, nursing or taking MAOIs. These statements have not been evaluated by the FDA and is not intended to diagnose, treat, cure or prevent any disease. Caution while driving or using heavy machinery.</p>
    <p class="info info--distributor">Distributed by:<br>VELMORA TRADING COMPANY BROOKHAVEN,<br>FL 32999</p>

    <div class="barcode-area">BAR CODE</div>
  </section>

</body>
</html>
```